Desert Basin Company Brochure

**** UPDATE 2-8-2014 ****

Size should be 11" X 17" or larger (tri or bi fold).

We're going to let the contest run it's full duration to allow for more time spent on designs.

No black backgrounds.

Consideration should be given to having the text be easy to read and in a nice, organized format.

*****************************

We're looking for an eye-catching, colorful brochure that will explain what we do, who we are... and what sets us apart from the competition.

Our company provides swimming pool service, repair, and custom renovations throughout the Phoenix, Arizona metropolitan area. These brochures will be hand-delivered to each prospective customer we visit.

The brochure will include images of our work, product logos, and a unique design that separates our company apart from the rest.

The brochure should be tri-fold. Although, if a designer wants to (or has better ideas) for a different lay-out, then we're open to seeing what can be done.

Colors we like: Blue, White, Silver, Copper, Green (accent color)

We like designs that are unique/different. Professional. Creative. Sleek. Sexy. Custom. We don't want the brochure to be "pretentious". We'd like for these brochures to leave a lasting impression with our prospective clients... and hopefully earn us more business.

We don't want the brochure to be too wordy, however if the designer feels we need to cut back (or add), let us know.

Our motto is "Every Ripple Counts".

You can view some of our projects, and what we're about either at our website (tidewellpools.example), Gatherly (www.facebook/tidewellpools), or Seekora+ (https://plus.google.com/+Tidewellpools). Thank you!

- Print-

(Front) Logo

Service - Repair - Renovation
555-347-9180
tidewellpools.example
service@tidewellpools.example
Like Us On Gatherly! Gatherly LOGO
Seekora Plus LOGO

(Body) Why Choose Us?

Thank you for the opportunity for our company to become your pool service provider!

We’re committed to providing the best customer service possible! At the end of the day you want your pool to be clean, clear, operational, and for your service provider to be available when you need them!

We’re licensed with the Sonoran Trades Licensing Board, Bonded, and Fully Insured.
A+ reviews with the Fair Merchant Council, Corra's Picks, Brivo, Olt, Gatherly, and Seekora!
All technicians are employees... not sub-contractors! Our employees are hard working, dependable, professional, and expected to follow our strict protocol for servicing your pool.
Flat-fee service rates! Any additional equipment repairs, maintenance, or chemical implementations are directly authorized by you!
No contracts! Our Service Level Agreement Form allows you to select your desired level of authorization for equipment repairs, filter maintenance, and extra chemical implementation programs.
Our uniformed technicians arrive in distinctive, clean GPS-tracked company trucks.
We leave detailed service slips after each service visit. In addition, all service visit information is electronically recorded and stored.
Easy, online account management to view and pay invoices or authorize estimates.
Invoices, estimates, questions, pictures, and video are communicated via e-mail!
Free service calls to diagnose equipment issues outside of our normal service.
10% Service Client Discount for all repairs and replacement items.
Tidewell Pools knows the importance of communication! We’re available by phone, email, or text all days of the week.

(Body) Our Methodology

We believe in 5 important factors in maintaining a clean, clear, and operational pool...

Good, Clean Water! Our local water supply contains high amounts of minerals. Pool chemicals add to this problem in a short amount of time. Our philosophy is to use the least amount of chemicals possible to achieve optimal water balance.
Efficient Water Flow! The invention of variable-speed pumps has enabled the ability to "dial in" proper water flow... while driving down energy costs.
Proper Filtration! Today’s high-capacity cartridge filters provide great filtration, save on wasted water from backwashing sand filters, and eliminate the need for water flow-restricting backwash valves.
Functioning Cleaning System! Having a working automatic cleaning system is vital in keeping the pool surface clean of debris and dirt... and free of staining.
A Dependable And Professional Pool Maintenance Technician! Our job is to not only oversee all of the items listed above... but to make sure your pool is in the best condition possible!

(Body) Equipment Repair & Installation

We’re educated on all phases of swimming pool equipment repair and installation... with a focus on energy-efficiency and optimum performance!

We’re an VRE & MQW Authorized Installer of variable-speed pool pumps. VRE & MQW trust us to properly install and calibrate all variable-speed pumps. We've been equipped to handle the new industry standards on variable-speed pumps since Arizona law went into effect January 1st, 2011.
We’re experts at acid washes and erasing the mineral build-up off of waterlines. All work is done in-house with our customized cleaning rig and trailer.
Heating systems. New efficiency standards have made installation and operation more affordable than ever.
Remote control automation systems. Technology now allows the user to easily view and control their entire pool system via a remote home computer, tablet, or phone!
Brilliant, color-changing LED lighting for pools and spas! The benefits of LED include brighter and broader displays... while lasting much longer than your typical light bulbs.
Salt systems provide a soft-water experience! In addition to the benefit of better feeling water, salt systems generate plenty of chlorine to keep your pool sanitized.

(Body) About Us

A native to Phoenix, Daniel Harrow founded Tidewell Pools in 2000. Our company was built from the ground up by way of hard work, word of mouth, and determination. Our company will always remain firmly grounded, and continue to develop systems that put our customers first!

Our philosophy is to treat every pool as if it were our own, run an efficient and organized business, and care for our employees.

Tidewell Pools is a yearly, proud contributor to the Saguaro Youth Clinic Swim Smart Day. Please educate and watch all children around water... every accident can be avoided.

(Back) Contact Us

Office: 555-347-9180 | Fax: 555-347-9186 | Email: service@tidewellpools.example
tidewellpools.example

Office / Warehouse Location
41572 West 8th Street, Suite 4
Phoenix, Arizona 85999
(NW of 8th Street & Mesquite Ridge Road)

AZ ROC: 731150, 731151, 731152, 604378

Target Market(s)

We target a market of pool owners, which typically have more disposable income.

30 - 75 years old.

Our clients range from first-time home buyers, self-employed, business professionals, doctors, landlords, thousandaires, millionaires.

Industry/Entity Type

Pool Service

Font styles to use
Serif

Colors
0355a3
cfdfed
ffffff
3176b5
eaf1f7

Requirements
Must have
• Must use provided images. We've included a few pool pictures, and will let you decide which ones to incorporate throughout the brochure.

Logos Used:
Tidewell Pools
Hydrovel
FMC
Corra's Picks
VRE
MQW
Saguaro Youth Clinic
Seekora+
Gatherly

Image pic of some of our trucks.

Nice to have
• Equipment images worked in.
Should not have
• Cartoonish fonts or design. No "Love" hearts!!

```html
<!DOCTYPE html>
<html lang="en">
<head>
<meta charset="utf-8">
<title>Tidewell Pools Brochure</title>
<link rel="stylesheet" href="https://fonts.googleapis.com/css2?family=Oswald:wght@500;600&family=PT+Sans:ital,wght@0,400;0,700;1,400&display=swap">
<style>
  :root {
    --royal: #2b3597;
    --brand: #0355a3;
    --brand-mid: #3176b5;
    --ice: #cfdfed;
    --mist: #eaf1f7;
    --paper: #fbfbf9;
    --ink: #2f3033;
    --grey: #8a8d91;
    --stage: #ebebeb;
    --warm-red: #c8463a;
    --leaf: #7aa84a;
  }
  * { box-sizing: border-box; margin: 0; padding: 0; }
  html, body { width: 1200px; height: 750px; overflow: hidden; }
  body { background: var(--stage); font-family: "PT Sans", sans-serif; color: var(--ink); position: relative; }

  .spread { position: absolute; top: 140px; width: 540px; height: 470px; display: flex; box-shadow: 0 6px 18px rgba(0,0,0,.18); }
  .spread--inside { left: 30px; }
  .spread--outside { left: 630px; }
  .page { position: relative; width: 270px; height: 470px; background: var(--paper); overflow: hidden; }
  .page + .page { border-left: 1px solid #e2e2e2; }

  .panel-title { font-weight: 700; font-size: 12.5px; color: var(--ink); margin-bottom: 5px; }
  .copy { font-size: 6.6px; line-height: 8.6px; text-align: justify; }
  .copy p { margin-bottom: 3px; }
  .bullets { list-style: none; }
  .bullets li { padding-left: 6px; text-indent: -6px; margin-bottom: 1px; }
  .bullets li::before { content: "•"; display: inline-block; width: 6px; text-indent: 0; }

  .why { position: absolute; left: 14px; right: 14px; top: 14px; }
  .photo { position: absolute; }
  .photo--desert-pool { left: 0; right: 0; bottom: 0; height: 92px; background: linear-gradient(180deg, #c9a36a 0%, #a88451 30%, #4f7fa6 55%, #2a5f93 100%); }
  .accent-square { position: absolute; width: 14px; height: 18px; background: var(--royal); }
  .accent-square--inside-left { left: 16px; bottom: 6px; }
  .accent-square--inside-right { right: 16px; bottom: 6px; }

  .equipment { position: absolute; left: 14px; right: 14px; top: 14px; }
  .photo--trucks { left: 0; right: 0; top: 246px; height: 66px; background: linear-gradient(180deg, #5a6a78 0%, #8fb3d6 45%, #2f78c4 70%, #3b3b3b 100%); }
  .about { position: absolute; left: 14px; right: 14px; top: 322px; }

  .outside-art { position: absolute; left: 0; top: 0; width: 540px; height: 470px; }
  .back-info { position: absolute; left: 14px; right: 14px; top: 14px; text-align: center; z-index: 1; }
  .service-area { font-size: 6.2px; letter-spacing: 1.4px; text-transform: uppercase; color: var(--grey); line-height: 9px; }
  .social { margin: 10px 0 0 42px; text-align: left; }
  .social-row { display: flex; align-items: center; gap: 5px; margin-bottom: 5px; }
  .social-mark { width: 15px; height: 15px; background: var(--brand); flex: none; }
  .social-mark--second { background: var(--warm-red); }
  .social-text { font-size: 6.5px; line-height: 7.5px; color: var(--ink); }
  .social-text strong { font-size: 8.5px; line-height: 10px; font-weight: 400; display: block; }
  .contact-lines { margin-top: 8px; font-size: 6.4px; line-height: 9px; text-align: right; color: var(--ink); }
  .address { margin-top: 6px; font-size: 6.8px; line-height: 9px; color: var(--ink); }
  .partners { margin-top: 12px; display: flex; justify-content: center; gap: 14px; align-items: center; }
  .partner-badge { width: 26px; height: 14px; background: var(--brand); }
  .partner-badge--red { background: var(--warm-red); }
  .partner-badge--round { width: 16px; height: 16px; border-radius: 50%; background: var(--brand-mid); }
  .partner-badge--green { width: 16px; height: 16px; border-radius: 50%; background: var(--leaf); }

  .brand-mark { position: absolute; display: flex; align-items: center; gap: 4px; font-weight: 700; color: var(--royal); z-index: 1; }
  .brand-mark::before { content: ""; width: 9px; height: 9px; border-radius: 50%; background: var(--royal); }
  .brand-mark--cover { right: 14px; top: 18px; font-size: 14px; }
  .brand-mark--back { left: 150px; top: 418px; font-size: 11px; }

  .cover-headline { position: absolute; right: 16px; top: 228px; text-align: right; font-family: "Oswald", sans-serif; font-weight: 600; font-size: 40px; line-height: 43px; color: var(--royal); letter-spacing: .5px; z-index: 1; }
  .cover-tagline { position: absolute; right: 16px; top: 366px; font-size: 6.8px; letter-spacing: 1.8px; color: var(--grey); text-transform: uppercase; z-index: 1; }
  .accent-square--cover { right: 16px; bottom: 6px; z-index: 1; }
</style>
</head>
<body>

<section class="spread spread--inside">
  <article class="page">
    <div class="why">
      <h2 class="panel-title">Why Choose Us?</h2>
      <div class="copy">
        <p>Thank you for the opportunity for our company to become your pool service provider!</p>
        <p>We’re committed to providing the best customer service possible! At the end of the day you want your pool to be clean, clear, operational, and for your service provider to be available when you need them!</p>
        <ul class="bullets">
          <li>We’re licensed with the Sonoran Trades Licensing Board, Bonded, and Fully Insured.</li>
          <li>A+ reviews with the Fair Merchant Council, Corra's Picks, Brivo, Olt, Gatherly, and Seekora!</li>
          <li>All technicians are employees... not sub-contractors! Our employees are hard working, dependable, professional, and expected to follow our strict protocol for servicing your pool.</li>
          <li>Flat-fee service rates! Any additional equipment repairs, maintenance, or chemical implementations are directly authorized by you!</li>
          <li>No contracts! Our Service Level Agreement Form allows you to select your desired level of authorization for equipment repairs, filter maintenance, and extra chemical implementation programs.</li>
          <li>Our uniformed technicians arrive in distinctive, clean GPS-tracked company trucks.</li>
          <li>We leave detailed service slips after each service visit. In addition, all service visit information is electronically recorded and stored.</li>
          <li>Easy, online account management to view and pay invoices or authorize estimates.</li>
          <li>Invoices, estimates, questions, pictures, and video are communicated via e-mail!</li>
          <li>Free service calls to diagnose equipment issues outside of our normal service.</li>
          <li>10% Service Client Discount for all repairs and replacement items.</li>
          <li>Tidewell Pools knows the importance of communication! We’re available by phone, email, or text all days of the week.</li>
        </ul>
      </div>
    </div>
    <div class="photo photo--desert-pool" role="img" aria-label="Photo of an infinity-edge pool overlooking the desert at sunset"></div>
    <div class="accent-square accent-square--inside-left"></div>
  </article>

  <article class="page">
    <div class="equipment">
      <h2 class="panel-title">Equipment Repair &amp; Installation</h2>
      <div class="copy">
        <p>We’re educated on all phases of swimming pool equipment repair and installation... with a focus on energy-efficiency and optimum performance!</p>
        <ul class="bullets">
          <li>We’re an VRE &amp; MQW Authorized Installer of variable-speed pool pumps. VRE &amp; MQW trust us to properly install and calibrate all variable-speed pumps. We've been equipped to handle the new industry standards on variable-speed pumps since Arizona law went into effect January 1st, 2011.</li>
          <li>We’re experts at acid washes and erasing the mineral build-up off of waterlines. All work is done in-house with our customized cleaning rig and trailer.</li>
          <li>Heating systems. New efficiency standards have made installation and operation more affordable than ever.</li>
          <li>Remote control automation systems. Technology now allows the user to easily view and control their entire pool system via a remote home computer, tablet, or phone!</li>
          <li>Brilliant, color-changing LED lighting for pools and spas! The benefits of LED include brighter and broader displays... while lasting much longer than your typical light bulbs.</li>
          <li>Salt systems provide a soft-water experience! In addition to the benefit of better feeling water, salt systems generate plenty of chlorine to keep your pool sanitized.</li>
        </ul>
      </div>
    </div>
    <div class="photo photo--trucks" role="img" aria-label="Photo of the company's branded blue service trucks parked in a row"></div>
    <div class="about">
      <h2 class="panel-title">About Us</h2>
      <div class="copy">
        <p>A native to Phoenix, Daniel Harrow founded Tidewell Pools in 2000. Our company was built from the ground up by way of hard work, word of mouth, and determination. Our company will always remain firmly grounded, and continue to develop systems that put our customers first!</p>
        <p>Our philosophy is to treat every pool as if it were our own, run an efficient and organized business, and care for our employees.</p>
        <p>Tidewell Pools is a yearly, proud contributor to the Saguaro Youth Clinic Swim Smart Day. Please educate and watch all children around water... every accident can be avoided.</p>
      </div>
    </div>
    <div class="accent-square accent-square--inside-right"></div>
  </article>
</section>

<section class="spread spread--outside">
  <article class="page">
    <div class="back-info">
      <p class="service-area">Providing swimming pool service,<br>repair, and custom renovations<br>throughout the Phoenix, Arizona metropolitan area</p>
      <div class="social">
        <div class="social-row"><span class="social-mark"></span><span class="social-text">Like us<strong>gatherly.example/tidewellpools</strong></span></div>
        <div class="social-row"><span class="social-mark social-mark--second"></span><span class="social-text">Join us<strong>circles.seekora.example/+tidewellpools</strong></span></div>
      </div>
      <p class="contact-lines">Office: 555-347-9180 | Fax: 555-347-9186<br>Email: service@tidewellpools.example | Web: www.tidewellpools.example</p>
      <p class="address">Office / Warehouse Location<br>41572 West 8th Street, Suite 4<br>Phoenix, Arizona 85999<br>(NW of 8th Street &amp; Mesquite Ridge Road)</p>
      <div class="partners">
        <span class="partner-badge"></span>
        <span class="partner-badge partner-badge--red"></span>
        <span class="partner-badge partner-badge--round"></span>
        <span class="partner-badge partner-badge--green"></span>
      </div>
    </div>
    <div class="brand-mark brand-mark--back">tidewellpools</div>
  </article>

  <article class="page">
    <div class="brand-mark brand-mark--cover">tidewellpools</div>
    <h1 class="cover-headline">SERVICE<br>REPAIR<br>RENOVATION</h1>
    <p class="cover-tagline">Economical but professional!</p>
    <div class="accent-square accent-square--cover"></div>
  </article>

  <svg class="outside-art" viewBox="0 0 540 470">
    <defs>
      <clipPath id="cover-photo-area">
        <path d="M282 193 L282 40.4 A165 165 0 0 1 434.6 193 Z"/>
      </clipPath>
      <clipPath id="back-photo-area">
        <path d="M258 202 L108.4 202 A162 162 0 0 0 258 351.6 Z"/>
      </clipPath>
      <linearGradient id="rock-pool" x1="0" y1="0" x2="1" y2="1">
        <stop offset="0" stop-color="#4d7a4a"/>
        <stop offset=".35" stop-color="#b39473"/>
        <stop offset=".65" stop-color="#4aa7c4"/>
        <stop offset="1" stop-color="#2d7fa6"/>
      </linearGradient>
      <linearGradient id="waterfall-pool" x1="0" y1="0" x2="0" y2="1">
        <stop offset="0" stop-color="#6f9a6a"/>
        <stop offset=".45" stop-color="#9c8468"/>
        <stop offset="1" stop-color="#3c9ac0"/>
      </linearGradient>
    </defs>
    <g role="img" aria-label="Photo of a rock-edged pool with a waterfall">
      <rect x="280" y="38" width="160" height="160" fill="url(#rock-pool)" clip-path="url(#cover-photo-area)"/>
    </g>
    <g role="img" aria-label="Photo of a grotto pool with palm trees and a rock waterfall">
      <rect x="104" y="200" width="156" height="156" fill="url(#waterfall-pool)" clip-path="url(#back-photo-area)"/>
    </g>
    <path class="ring-arc" d="M270 20 A185 185 0 0 1 452 237" fill="none" stroke="var(--royal)" stroke-width="22"/>
    <path class="ring-arc" d="M90 190 A180 180 0 0 0 270 370" fill="none" stroke="var(--royal)" stroke-width="22"/>
  </svg>
</section>

</body>
</html>
```